LM-Steuerberatung WordPress Site fully implemented (tax advisor)

Hello!
I need a little Wordpress Site for my newly founded Tax-Advisor Company.
I am a one-man Office advising in the area of Crypto-Currency.
PLEASE only provide a Design, if you can also Implement a WP-Site afterwards on an existing Webspace.

Please find the Content and Website-Description in the attached Document

Language for the Website is German (for now)

Target Market(s)

Tax-Advisory (specialized in Crypto Currency)

Coding

Coded - Design and coding required

Number of Pages Required

5+ page

Font styles to use
Sans Serif

Requirements
Must have
• Wordpress Implementation afterwards - Details according to attached Project Information Document

```html
<!DOCTYPE html>
<html lang="de">
<head>
<meta charset="utf-8">
<title>LM-Steuerberatung</title>
<link rel="stylesheet" href="https://fonts.googleapis.com/css2?family=Montserrat:wght@400;500;600;700&display=swap">
<style>
  :root {
    --navy: #1b2a44;
    --ink: #1f2430;
    --white: #ffffff;
    --deep: #0b2747;
    --mid: #1e4d72;
    --teal: #3fb0c9;
    --photo-light: #9aa4a8;
    --photo-dark: #3a3f44;
  }
  * { margin: 0; padding: 0; box-sizing: border-box; }
  html, body { width: 1200px; height: 699px; overflow: hidden; }
  body { font-family: "Montserrat", sans-serif; background: var(--white); position: relative; }

  .site-header { position: absolute; top: 0; left: 0; width: 1200px; height: 82px; background: var(--white); }
  .brand { position: absolute; left: 69px; top: 26px; display: flex; align-items: center; gap: 10px; }
  .brand-mark { width: 26px; height: 26px; background: var(--navy); }
  .brand-name { font-weight: 700; font-size: 17px; color: var(--navy); letter-spacing: 0.3px; }

  .main-nav { position: absolute; top: 31px; left: 429px; display: flex; gap: 29px; font-size: 15px; color: var(--ink); }
  .main-nav a { color: inherit; text-decoration: none; }
  .main-nav .active { font-weight: 600; }
  .caret { display: inline-block; margin-left: 4px; border-left: 4px solid transparent; border-right: 4px solid transparent; border-top: 5px solid var(--ink); vertical-align: middle; }
  .cta-button { position: absolute; left: 941px; top: 20px; width: 191px; height: 43px; background: var(--navy); color: var(--white); font-size: 15px; font-weight: 500; display: flex; align-items: center; justify-content: center; }

  .hero { position: absolute; top: 82px; left: 0; width: 1200px; height: 617px; overflow: hidden; }
  .hero-photo { position: absolute; inset: 0; background: linear-gradient(180deg, var(--photo-light) 0%, #6f777c 45%, var(--photo-dark) 100%); }
  .hero-data { position: absolute; left: 0; top: 0; width: 620px; height: 617px;
    background: radial-gradient(ellipse at 30% 65%, rgba(63,176,201,0.55) 0%, rgba(30,77,114,0.4) 40%, transparent 70%),
                linear-gradient(90deg, var(--deep) 0%, var(--mid) 55%, rgba(30,77,114,0) 100%); }

  .hero-content { position: absolute; left: 112px; top: 0; color: var(--white); }
  .hero-title { position: absolute; top: 80px; width: 520px; font-size: 43px; font-weight: 700; line-height: 55px; }
  .hero-lead { position: absolute; top: 208px; width: 500px; font-size: 15px; font-weight: 500; line-height: 32px; }
  .quote-label { position: absolute; top: 315px; font-size: 19px; font-weight: 700; white-space: nowrap; }
  .quote-text { position: absolute; top: 358px; width: 420px; font-size: 15px; font-weight: 500; line-height: 33px; }
  .hero-button { position: absolute; top: 489px; left: -1px; width: 286px; height: 44px; border: 2px solid var(--white); color: var(--white); font-size: 15px; font-weight: 600; display: flex; align-items: center; justify-content: center; }

  .slider-nav { position: absolute; left: 1136px; top: 255px; color: var(--white); font-size: 15px; font-weight: 600; }
  .slider-nav li { list-style: none; display: flex; align-items: center; gap: 8px; height: 45px; }
  .slider-nav li::before { content: ""; width: 5px; height: 5px; background: var(--white); }
  .slider-nav li.current { color: var(--navy); }
  .slider-nav li.current::before { background: var(--navy); }
</style>
</head>
<body>
  <header class="site-header">
    <div class="brand"><span class="brand-mark"></span><span class="brand-name">LM STEUERBERATUNG</span></div>
    <nav class="main-nav">
      <a class="active">Home</a>
      <a>Leistungen<span class="caret"></span></a>
      <a>Über mich</a>
      <a>Kontakt</a>
      <a>Impressum</a>
    </nav>
    <a class="cta-button">Termin Vereinbaren</a>
  </header>

  <section class="hero">
    <div class="hero-photo" role="img" aria-label="Foto eines lächelnden Beraters mit Brille, der am Laptop sitzt und telefoniert, vor einem Bürofenster"></div>
    <div class="hero-data" role="img" aria-label="Digitale Datenströme aus leuchtenden Punkten in Blau und Türkis"></div>
    <div class="hero-content">
      <h1 class="hero-title">Willkommen bei LM-Steuerberatung!</h1>
      <p class="hero-lead">Ihrem Spezialisten bei allen steuerlichen Themen rund um Einkünfte &amp; Vermögen aus Krypto-Assets.</p>
      <h2 class="quote-label">Quotations:</h2>
      <p class="quote-text">Dann mach ich eine Schweizer Holding-Ge-sellschaft– dort zahlt man fast keine Steuern</p>
      <a class="hero-button">Weiter zu unseren Leistungen</a>
    </div>
    <ul class="slider-nav">
      <li class="current">1</li>
      <li>2</li>
      <li>3</li>
    </ul>
  </section>
</body>
</html>
```